Federal IT Consulting Company - Brisolux Consulting Group

We're seeking a skilled web designer to create a modern, bold, and engaging WordPress website for Brisolux Consulting Group, LLC. Our company specializes in federal IT consulting, and our name is a play on "Brightening Solutions." The website should reflect our expertise in the federal technology marketplace and position us as a trusted partner for clients navigating their IT journey.

contact: info@brisoluxgrp-example.com

Current Status

WordPress is already installed on our hosting account
We have an existing logo (may need modernization)

Design Requirements

Style:

Modern and visually striking design
Bold elements to convey confidence and expertise
Incorporate the concept of "brightening solutions" into the design

Features:

Modern UX sliders for dynamic content presentation
Eye-catching, high-quality images (stock photos to be sourced by the designer)
Responsive design for all devices

Color Scheme:

To be proposed by the designer, should align with our brand and convey trust and technological expertise

Logo:

Evaluate our current logo
Create a transparent background version if needed
Propose modernization if deemed necessary

Accessibility:

Ensure design elements are accessible to users with disabilities
Use high contrast ratios for text and background colors
Provide text alternatives for non-text content

Website Structure
Create the following pages, with the possibility of subpages:

Home
Services
About
Contact

Specific Page Requirements
Home Page

Striking hero section with a clear value proposition
Overview of our services
Client testimonials or trust indicators

Services Page

Detailed list of our IT consulting services
Clear explanation of how we help navigate the federal IT landscape

About Page

Company history and mission
Team highlights (if applicable)
Our approach to federal IT consulting

Contact Page

Contact form
Other contact methods (phone, email)

Technical Requirements

Fully responsive design
SEO best practices implemented
Fast loading times
Integration with necessary plugins (to be discussed)
Training on how to update and maintain the site
Full compliance with Web Content Accessibility Guidelines (WCAG) 2.1 Level AA
Adherence to Section 508 standards for federal website accessibility
Implementation of necessary features for ADA compliance
Updates

Designs look the same

Target Market(s)

US Federal Govt customers looking for IT support.

Industry/Entity Type

IT Consulting

Coding

Coded - Design and coding required

Colors
0054AA
0677BA
7BADD7
CADEEF
E8F1F8
0094D4
00A9DD
6FCCEA
C7EBF8
E9F6FB
00AB8E
00BBA5
67D7C9
C6EFE9
E9F9F6

```html
<!DOCTYPE html>
<html lang="en">
<head>
<meta charset="utf-8">
<title>About Us – Brisolux Consulting Group</title>
<link rel="stylesheet" href="https://fonts.googleapis.com/css2?family=Exo+2:wght@600;700;800&family=Montserrat:wght@400;500;600&display=swap">
<style>
:root{
  --navy:#25246e;
  --navy-deep:#1b1a52;
  --accent:#7470d3;
  --accent-light:#8f8be6;
  --ink:#111118;
  --body:#2b2b33;
  --tint:#f2f2fb;
  --white:#ffffff;
  --line:#3b3a7a;
  --head:"Exo 2",sans-serif;
  --text:"Montserrat",sans-serif;
}
*{margin:0;padding:0;box-sizing:border-box}
html,body{width:1200px;height:2634px;overflow:hidden}
body{position:relative;background:var(--white);font-family:var(--text);color:var(--body)}
a{color:inherit;text-decoration:none}
.abs{position:absolute}

/* header */
.site-header{left:0;top:0;width:1200px;height:70px;background:var(--white)}
.brand{display:flex;align-items:center;gap:10px;left:141px;top:14px}
.brand-dot{width:40px;height:40px;border-radius:50%;border:4px solid var(--navy)}
.brand-name{font-family:var(--head);font-weight:800;font-size:30px;letter-spacing:1px;color:var(--navy)}
.main-nav{left:682px;top:26px;display:flex;gap:34px;font-size:13px;font-weight:500;color:var(--ink)}
.main-nav .current{color:var(--accent)}
.btn-contact{left:937px;top:16px;width:122px;height:39px;border-radius:20px;background:var(--navy);color:var(--white);font-size:13px;font-weight:500;display:flex;align-items:center;justify-content:center}

/* hero */
.page-hero{left:0;top:70px;width:1200px;height:283px;background:linear-gradient(90deg,#f1f2f4 0%,#e6e8ec 35%,#c9ccd2 60%,#b7bcc2 85%,#4d5a4a 100%)}
.page-title{left:141px;top:168px;font-family:var(--head);font-weight:800;font-size:35px;color:var(--ink)}
.breadcrumb{left:141px;top:220px;font-size:14px;font-weight:600;color:var(--ink);display:flex;align-items:center;gap:7px}
.breadcrumb .here{color:var(--accent)}

/* shared headings */
.sec-title{font-family:var(--head);font-weight:800;font-size:36px;color:var(--ink);line-height:1}
.sec-title .lead{color:var(--accent)}
.rule{height:3px;width:70px;background:var(--navy)}
.copy p{font-size:12.4px;line-height:20.5px;margin-bottom:10px}

/* about */
.about-photo{left:141px;top:438px;width:395px;height:460px;border-radius:60px 0 60px 0;background:linear-gradient(135deg,#1d3f86 0%,#6f86b3 40%,#d9dde4 70%,#2c3552 100%)}
.about-title{left:613px;top:448px}
.about-rule{left:613px;top:490px}
.about-copy{left:613px;top:514px;width:446px}

/* approach */
.approach{left:0;top:982px;width:1200px;height:346px;background:var(--tint)}
.approach-title{left:0;top:1042px;width:1200px;text-align:center}
.approach-rule{left:565px;top:1084px}
.approach-copy{left:279px;top:1114px;width:642px;text-align:center}

/* mission */
.mission-title{left:141px;top:1435px}
.mission-rule{left:141px;top:1476px}
.mission-copy{left:141px;top:1500px;width:446px}
.mission-photo{left:664px;top:1413px;width:395px;height:341px;border-radius:0 60px 0 60px;background:linear-gradient(135deg,#2f2a22 0%,#5b4a36 40%,#2b3140 70%,#1d1f28 100%)}

/* experts */
.experts-title{left:0;top:1848px;width:1200px;text-align:center}
.experts-rule{left:565px;top:1893px}
.team{left:0;top:1931px;width:1200px}
.member{position:absolute;top:0;width:200px;text-align:center}
.member-photo{width:183px;height:183px;border-radius:50%;margin:0 auto;background:radial-gradient(circle at 50% 40%,#f4f4fb 0%,#dcdbf3 60%,#c9c7ee 100%)}
.member-name{margin-top:18px;font-family:var(--head);font-weight:700;font-size:16px;color:var(--ink)}
.member-role{margin-top:4px;font-size:11px;color:var(--accent)}
.member-links{margin-top:12px;display:flex;justify-content:center;gap:9px}
.social{width:33px;height:33px;border-radius:50%;background:var(--accent);display:block}

/* footer */
.site-footer{left:0;top:2302px;width:1200px;height:332px;background:var(--navy-deep)}
.footer-brand{left:141px;top:2378px;display:flex;align-items:center;gap:12px}
.footer-brand .brand-dot{width:52px;height:52px;border-color:var(--white)}
.footer-brand .brand-name{color:var(--white);font-size:38px}
.foot-col{color:var(--white)}
.foot-col h3{font-family:var(--head);font-weight:700;font-size:16px;color:var(--accent-light);margin-bottom:12px}
.foot-col li{list-style:none;font-size:12.5px;margin-bottom:11px;color:var(--white)}
.col-links{left:511px;top:2383px}
.col-res{left:673px;top:2379px}
.col-contact{left:851px;top:2379px;width:230px}
.col-contact li{display:flex;gap:10px;align-items:flex-start;line-height:17px;margin-bottom:14px}
.col-contact svg{flex:none;margin-top:1px}
.footer-rule{left:141px;top:2569px;width:918px;height:1px;background:var(--line)}
.copyright{left:141px;top:2593px;font-size:12.5px;color:var(--white)}
.footer-social{left:908px;top:2585px;display:flex;gap:10px}
.footer-social .social{width:30px;height:30px;background:#6f6bcf}
</style>
</head>
<body>

<header class="site-header abs">
  <a class="brand abs" href="#"><span class="brand-dot"></span><span class="brand-name">BRISOLUX</span></a>
  <nav class="main-nav abs"><a href="#">Home</a><a class="current" href="#">About Us</a><a href="#">Services</a></nav>
  <a class="btn-contact abs" href="#">Contact Us</a>
</header>

<section class="page-hero abs" role="img" aria-label="Photo of a white domed government building under a cloudy sky"></section>
<h1 class="page-title abs">ABOUT US</h1>
<div class="breadcrumb abs">
  <span>HOME</span>
  <svg width="12" height="10" viewBox="0 0 12 10" aria-hidden="true"><path d="M1 1l4 4-4 4M6 1l4 4-4 4" fill="none" stroke="#111118" stroke-width="1.8"/></svg>
  <span class="here">ABOUT US</span>
</div>

<div class="about-photo abs" role="img" aria-label="Photo of colleagues working on laptops in a bright office"></div>
<h2 class="sec-title about-title abs"><span class="lead">ABOUT</span> BRISOLUX</h2>
<div class="rule about-rule abs"></div>
<div class="copy about-copy abs">
  <p>Lorem Ipsum is simply dummy text of the printing and typesetting industry. It is a long established fact that a reader will be distracted by the readable content of a page when looking at its layout. The point of using Lorem Ipsum is that it has a more-or-less normal distribution of letters, as opposed to using 'Content here, content here', making it look like readable English. t uses a dictionary of over 200 Latin words, combined with a handful of model sentence structures, to generate Lorem Ipsum which looks reasonable.</p>
  <p>Many desktop publishing packages and web page editors now use Lorem Ipsum as their default model text, and a search for 'lorem ipsum' will uncover many web sites still in their infancy. Various versions have evolved over the years, sometimes by accident, sometimes on purpose (injected humour and the like). There are many variations of passages of Lorem Ipsum available, but the majority have suffered alteration in some form, by injected humour, or randomised words which don't look even slightly believable.</p>
</div>

<section class="approach abs"></section>
<h2 class="sec-title approach-title abs"><span class="lead">OUR</span> APPROACH</h2>
<div class="rule approach-rule abs"></div>
<div class="copy approach-copy abs">
  <p>Lorem Ipsum is simply dummy text of the printing and typesetting industry. Lorem Ipsum has been the industry's standard dummy text ever since the 1500s, when an unknown printer took a galley of type and scrambled it to make a type specimen book. It has survived not only five centuries, but also the leap into electronic typesetting, remaining essentially unchanged. It was popularised in the 1960s with the release of Letraset sheets containing. There are many variations of passages of Lorem Ipsum available, but the majority have suffered alteration in some form, by injected humour, or randomised words which don't look even slightly believable. If you are going to use a passage of Lorem Ipsum, you need to be sure there isn't anything embarrassing hidden in the middle of text.</p>
</div>

<h2 class="sec-title mission-title abs"><span class="lead">OUR</span> MISSION</h2>
<div class="rule mission-rule abs"></div>
<div class="copy mission-copy abs">
  <p>Lorem Ipsum is simply dummy text of the printing and typesetting industry. It is a long established fact that a reader will be distracted by the readable content of a page when looking at its layout. The point of using Lorem Ipsum is that it has a more-or-less normal distribution of letters, as opposed to using 'Content here, content here', making it look like readable English.</p>
  <p>Many desktop publishing packages and web page editors now use Lorem Ipsum as their default model text, and a search for 'lorem ipsum' will uncover many web sites still in their infancy. Various versions have evolved over the years, sometimes by accident.</p>
</div>
<div class="mission-photo abs" role="img" aria-label="Photo of two consultants reviewing charts at a table"></div>

<h2 class="sec-title experts-title abs"><span class="lead">MEET THE</span> OUR EXPERTS</h2>
<div class="rule experts-rule abs"></div>
<div class="team abs">
  <div class="member" style="left:166px">
    <div class="member-photo" role="img" aria-label="Portrait of Mara Venn"></div>
    <div class="member-name">Mara Venn</div><div class="member-role">Web Designer</div>
    <div class="member-links"><a class="social" href="#" aria-label="Professional profile"></a><a class="social" href="#" aria-label="Social profile"></a></div>
  </div>
  <div class="member" style="left:388px">
    <div class="member-photo" role="img" aria-label="Portrait of Tobin Arlow"></div>
    <div class="member-name">Tobin Arlow</div><div class="member-role">Web Designer</div>
    <div class="member-links"><a class="social" href="#" aria-label="Professional profile"></a><a class="social" href="#" aria-label="Social profile"></a></div>
  </div>
  <div class="member" style="left:611px">
    <div class="member-photo" role="img" aria-label="Portrait of Ines Halvor"></div>
    <div class="member-name">Ines Halvor</div><div class="member-role">Web Designer</div>
    <div class="member-links"><a class="social" href="#" aria-label="Professional profile"></a><a class="social" href="#" aria-label="Social profile"></a></div>
  </div>
  <div class="member" style="left:833px">
    <div class="member-photo" role="img" aria-label="Portrait of Owen Pratley"></div>
    <div class="member-name">Owen Pratley</div><div class="member-role">Web Designer</div>
    <div class="member-links"><a class="social" href="#" aria-label="Professional profile"></a><a class="social" href="#" aria-label="Social profile"></a></div>
  </div>
</div>

<footer class="site-footer abs"></footer>
<div class="footer-brand abs"><span class="brand-dot"></span><span class="brand-name">BRISOLUX</span></div>
<div class="foot-col col-links abs">
  <h3>Quick Links</h3>
  <ul><li>Home</li><li>About Us</li><li>Services</li></ul>
</div>
<div class="foot-col col-res abs">
  <h3>Resources</h3>
  <ul><li>Privacy Policy</li><li>Terms Of Service</li></ul>
</div>
<div class="foot-col col-contact abs">
  <h3>Contact Info</h3>
  <ul>
    <li><svg width="16" height="18" viewBox="0 0 16 18" aria-hidden="true"><path d="M8 1a5 5 0 0 0-5 5c0 4 5 9 5 9s5-5 5-9a5 5 0 0 0-5-5z" fill="none" stroke="#8f8be6" stroke-width="1.6"/><circle cx="8" cy="6" r="1.8" fill="#8f8be6"/><ellipse cx="8" cy="16.5" rx="6" ry="1.2" fill="none" stroke="#8f8be6"/></svg><span>48 Sample Avenue, Suite 210,<br>Example City 0000</span></li>
    <li><svg width="17" height="13" viewBox="0 0 17 13" aria-hidden="true"><rect x="0" y="0" width="17" height="13" rx="2" fill="#8f8be6"/><path d="M1 2l7.5 5L16 2" fill="none" stroke="#1b1a52" stroke-width="1.4"/></svg><span>info@brisoluxgrp-example.com</span></li>
    <li><svg width="16" height="16" viewBox="0 0 16 16" aria-hidden="true"><path d="M3 1l3 3-1.5 2c1 2 3 4 5 5L11.5 9.5l3 3-1.5 2.5C7 15 1 9 .5 3z" fill="#8f8be6"/></svg><span>555-010-4821</span></li>
  </ul>
</div>
<div class="footer-rule abs"></div>
<p class="copyright abs">© 2024 Brisolux Consulting Group. All rights reserved.</p>
<div class="footer-social abs">
  <a class="social" href="#" aria-label="Photo sharing profile"></a>
  <a class="social" href="#" aria-label="Microblog profile"></a>
  <a class="social" href="#" aria-label="Social profile"></a>
  <a class="social" href="#" aria-label="Professional profile"></a>
</div>

</body>
</html>
```